Book Cover for a Short Story called “Leaving Harbor"

Pretty Straightforward. Looking for a 5.5X8.5 book cover. The story is a very short (40 pages) story about a man who moves from Greece to Canada in 1920. I have three photos to provide. One is the house that he left in greece. THen I have photos of him and his wife who he met in Toronto. I think I want the house photo on the front...
I will need cover for paper back and e-book. The ISBN numbers are:

ISBN: 978-1-5523094-2-7 (e-book)
ISBN: 978-1-5523094-1-0 (paperback)

If you want you can read it at https://kevinmarlow.example/fiction/leaving-harbor/

Colors
0094D4
00A9DD
6FCCEA
C7EBF8
E9F6FB

Requirements
Must have
• Room for a blurb about the book on the back cover. ISBN Number

```html
<!DOCTYPE html>
<html lang="en">
<head>
<meta charset="utf-8">
<title>Leaving Harbor — Book Cover</title>
<link rel="stylesheet" href="https://fonts.googleapis.com/css2?family=EB+Garamond:wght@400;500&family=Open+Sans:wght@400;700&display=swap">
<style>
  :root {
    --stage: #262626;
    --back-paper: #ffffff;
    --front-paper-top: #d8ceb8;
    --front-paper-mid: #e6dcc6;
    --ink: #333027;
    --body-ink: #2e2b26;
    --portrait-dark: #2a3a5c;
    --portrait-mid: #5d6f94;
    --house-light: #cfc6b3;
    --house-mid: #9d947f;
    --house-dark: #6e665a;
  }
  * { margin: 0; padding: 0; box-sizing: border-box; }
  html, body { width: 1200px; height: 1200px; overflow: hidden; background: var(--stage); }
  .spread {
    position: absolute; left: 33px; top: 163px; width: 1134px; height: 874px;
    display: flex;
  }
  .back-cover {
    position: relative; width: 571px; height: 100%; background: var(--back-paper);
    font-family: "Open Sans", Arial, sans-serif; color: var(--body-ink);
  }
  .back-title {
    position: absolute; left: 0; width: 100%; top: 115px; text-align: center;
    font-family: "EB Garamond", Georgia, serif; font-weight: 400; font-size: 54px;
    color: var(--ink); line-height: 1;
  }
  .blurb {
    font-size: 12px; line-height: 18px; text-align: justify; position: absolute;
  }
  .blurb-intro { left: 58px; width: 460px; top: 191px; }
  .blurb-column { left: 266px; width: 252px; top: 327px; }
  .blurb-column p + p { margin-top: 18px; }
  .author-portrait {
    position: absolute; left: 14px; top: 303px; width: 252px; height: 380px;
    background:
      linear-gradient(to bottom, rgba(255,255,255,0) 55%, #ffffff 96%),
      radial-gradient(ellipse 34% 26% at 45% 22%, #d9b8a3 0 60%, transparent 62%),
      radial-gradient(ellipse 70% 60% at 50% 78%, var(--portrait-mid) 0, var(--portrait-dark) 60%, transparent 72%);
  }
  .isbn {
    position: absolute; left: 41px; top: 800px; font-size: 12px; font-weight: 700;
  }
  .front-cover {
    position: relative; flex: 1; height: 100%; overflow: hidden;
    background: linear-gradient(100deg, var(--front-paper-top), var(--front-paper-mid) 60%, #ddd3bd);
  }
  .author-name {
    position: absolute; left: 0; width: 100%; top: 132px; text-align: center;
    font-family: "EB Garamond", Georgia, serif; font-size: 37px; letter-spacing: 0.2em;
    color: var(--ink); text-indent: 0.2em; line-height: 1;
  }
  .front-title {
    position: absolute; left: 0; width: 100%; top: 200px; text-align: center;
    font-family: "EB Garamond", Georgia, serif; font-weight: 500; font-size: 146px;
    line-height: 156px; color: var(--ink);
  }
  .house-photo {
    position: absolute; left: 0; right: 0; bottom: 0; height: 330px;
    background:
      linear-gradient(to bottom, var(--front-paper-mid) 0%, rgba(230,220,198,0) 28%),
      linear-gradient(to right, var(--house-mid), var(--house-light) 45%, var(--house-mid) 80%, var(--house-dark)),
      var(--house-mid);
  }
</style>
</head>
<body>
  <main class="spread">
    <section class="back-cover">
      <h2 class="back-title">Leaving Harbor</h2>
      <p class="blurb blurb-intro">Lorem ipsum dolor sit amet, consectetur adipiscing elit, sed do eiusmod tempor incididunt ut labore et dolore magna aliqua. Quis ipsum suspendisse ultrices gravida. Risus commodo viverra maecenas accumsan lacus vel facilisis. Lorem ipsum dolor sit amet, consectetur adipiscing elit, sed do eiusmod tempor incididunt ut labore et dolore magna aliqua.</p>
      <div class="author-portrait" role="img" aria-label="Portrait photo of the author in a navy blazer, arms crossed, fading to white"></div>
      <div class="blurb blurb-column">
        <p>Quis ipsum suspendisse ultrices gravida. Risus commodo viverra maecenas accumsan lacus vel facilisis. Lorem ipsum dolor sit amet, consectetur adipiscing elit, sed do eiusmod tempor incididunt ut labore et dolore magna aliqua. Quis ipsum suspendisse ultrices gravida. Risus commodo viverra maecenas accumsan lacus vel facilisis.</p>
        <p>Quis ipsum suspendisse ultrices gravida. Risus commodo viverra maecenas accumsan lacus vel facilisis. Lorem ipsum dolor sit amet, consectetur adipiscing elit, sed do eiusmod tempor incididunt ut labore et dolore magna aliqua. Quis ipsum suspendisse ultrices gravida. Risus commodo viverra maecenas accumsan lacus vel facilisis.</p>
      </div>
      <p class="isbn">ISBN: 978-1-5523094-1-0</p>
    </section>
    <section class="front-cover">
      <p class="author-name">KEVIN MARLOW</p>
      <h1 class="front-title">Leaving<br>Harbor</h1>
      <div class="house-photo" role="img" aria-label="Sepia photograph of an old stone house with a tiled roof and shuttered windows in Greece"></div>
    </section>
  </main>
</body>
</html>
```